Lifestyle Coaching comp needs wordpress design. We focus on strong mindsets, fitness and nutrition

BrenVigor Lifestyle Coaching needs a wordpress site. Our tagline for now (may change) is Mindset Mastery.Fitness Badassery. Sustainable Nutrition
Our logo is below. Would like to see some complimentary colors to liven it up. Clients need to come to site and get immediate professional, but fun feel. They need to have the impression that we are the last destination in their journey to wellness. Blogging, workout videos, pictures

Target Market(s)

Mostly women ages 20+

Industry/Entity Type

Nutrition

Colors
33a6d7
86cae7
ceeaf6
cfdeed
5c5c5c
cbcbcb
474747

Requirements
Must have
• A strong, badass feel :) While not being intimidating
Nice to have
• Fun fonts. Love the font in my logo
Should not have
• Pics, logos of flowers, heads, fruit.

```html
<!DOCTYPE html>
<html lang="en">
<head>
<meta charset="utf-8">
<title>BrenVigor Lifestyle Coaching</title>
<link href="https://fonts.googleapis.com/css2?family=Raleway:wght@400;500;600&family=Open+Sans:ital,wght@0,400;0,600;1,400&family=Arvo&display=swap" rel="stylesheet">
<style>
:root{
  --blue:#33a6d7;
  --blue-light:#86cae7;
  --sky:#ceeaf6;
  --mist:#cfdeed;
  --grey:#5c5c5c;
  --grey-light:#cbcbcb;
  --charcoal:#474747;
  --ink:#2b2b2b;
  --nav:#3a3a3a;
  --card:#f3f3f3;
  --white:#ffffff;
}
*{margin:0;padding:0;box-sizing:border-box}
html,body{width:1200px;height:2353px;overflow:hidden;background:var(--white)}
body{font-family:"Open Sans",sans-serif;color:var(--grey)}
.page{position:relative;width:1200px;height:2353px;overflow:hidden}
.abs{position:absolute}

.site-header{left:0;top:0;width:1200px;height:115px;background:linear-gradient(#ffffff,#f2f2f2)}
.brand{left:130px;top:30px;display:flex;align-items:center;gap:12px}
.brand-mark{width:40px;height:40px;border-radius:50%;background:var(--blue)}
.brand-name{font-family:"Raleway",sans-serif;font-weight:600;font-size:24px;color:var(--blue);letter-spacing:1px;line-height:1.1}
.brand-name small{display:block;font-size:11px;letter-spacing:2px}
.social-top{left:921px;top:46px;display:flex;gap:8px}
.social-top span{width:31px;height:31px;border-radius:50%}

.main-nav{left:0;top:115px;width:1200px;height:51px;background:linear-gradient(#474747,#2f2f2f)}
.main-nav a{position:absolute;top:0;height:51px;line-height:51px;color:var(--white);font-family:"Raleway",sans-serif;font-size:14px;text-decoration:none;transform:translateX(-50%);white-space:nowrap}
.main-nav a.active{background:var(--blue);width:105px;text-align:center;left:182px}

.hero{left:0;top:166px;width:1200px;height:650px;background:linear-gradient(160deg,#cfe6f5 0%,#eaf4fb 45%,#d7e9f4 80%,#b9d48a 100%)}
.hero-photo{left:200px;top:0;width:500px;height:650px;background:linear-gradient(#d8e4ee,#c9c4dc 55%,#e4e4ec)}
.hero-arrow{top:294px;width:42px;height:42px;background:rgba(160,160,160,.8)}
.hero-arrow.left{left:0}.hero-arrow.right{right:0}
.hero-arrow svg{display:block;margin:13px auto}
.hero-copy{right:130px;top:240px;text-align:right;color:var(--ink)}
.hero-copy h1{font-family:"Arvo",serif;font-weight:400;font-size:35px;line-height:49px}
.hero-copy p{font-family:"Open Sans",sans-serif;font-size:18px;line-height:28px;margin-top:26px;color:var(--charcoal)}

.section-title{width:1200px;left:0;text-align:center;font-family:"Raleway",sans-serif;font-weight:400;font-size:29px;color:var(--ink)}
.section-title em{font-style:normal;color:var(--blue)}
.welcome-text{left:141px;top:938px;width:919px;text-align:center;font-size:12.5px;line-height:25px;color:var(--grey)}
.btn{left:543px;top:1041px;width:117px;height:40px;background:var(--blue);color:var(--white);border-radius:2px;font-size:13px;text-align:center;line-height:40px;font-weight:600}
.divider{left:130px;top:1112px;width:941px;height:1px;background:#e3e3e3}
.pictures-sub{left:0;width:1200px;top:1200px;text-align:center;font-size:15px;color:var(--ink)}
.gallery{top:1249px;width:220px;height:155px}

.blog-title{left:133px;top:1460px;font-family:"Raleway",sans-serif;font-size:30px;color:var(--ink)}
.blog-nav{top:1465px;width:27px;height:27px;border-radius:50%;background:var(--grey)}
.blog-nav svg{display:block;margin:8px auto}
.post{top:1511px;width:282px;height:138px;background:var(--card);padding:16px 20px;font-size:12.5px;line-height:24px;color:var(--grey)}
.post::after{content:"";position:absolute;left:28px;bottom:-16px;border:14px solid transparent;border-top:16px solid var(--card);border-bottom:0}
.author{top:1678px;display:flex;align-items:center;gap:16px}
.avatar{width:74px;height:74px;border-radius:50%;background:linear-gradient(#e6d5c8,#c9a994);border:3px solid #e6e6e6}
.author b{display:block;font-size:12px;color:var(--blue);font-weight:600}
.author i{font-size:12.5px;color:#9a9a9a}

.video{left:130px;top:1807px;width:940px;height:386px;background:linear-gradient(90deg,#4a4d52,#5e6066 60%,#3f4044)}
.video h2{position:absolute;left:0;width:940px;top:50px;text-align:center;font-family:"Raleway",sans-serif;font-weight:400;font-size:30px;color:var(--white)}
.video svg{position:absolute;left:427px;top:170px}

.site-footer{left:0;top:2237px;width:1200px;height:116px;background:#3d3d3d}
.footer-links{left:130px;top:34px;font-size:12.5px;color:var(--white);display:flex;gap:14px}
.copyright{left:130px;top:64px;font-size:12px;color:var(--white)}
.social-foot{left:896px;top:48px;display:flex;gap:6px}
.social-foot span{width:31px;height:31px;border-radius:50%;background:var(--white)}
</style>
</head>
<body>
<div class="page">
  <header class="site-header abs">
    <div class="brand abs"><span class="brand-mark"></span><div class="brand-name">BrenVigor<small>LIFESTYLE COACHING</small></div></div>
    <div class="social-top abs">
      <span style="background:#1d5aa8"></span><span style="background:#2da7e0"></span><span style="background:#f39a1d"></span><span style="background:#c9352a"></span>
    </div>
  </header>

  <nav class="main-nav abs">
    <a class="active" href="#">HOME</a>
    <a href="#" style="left:298px">ABOUT US</a>
    <a href="#" style="left:427px">SERVICES</a>
    <a href="#" style="left:566px">TESTIMONIALS</a>
    <a href="#" style="left:715px">OUR WORKS</a>
    <a href="#" style="left:839px">BLOG</a>
    <a href="#" style="left:958px">CONTACT US</a>
  </nav>

  <section class="hero abs">
    <div class="hero-photo abs" role="img" aria-label="Smiling woman in sportswear tying her running shoe on grass under a blue sky"></div>
    <div class="hero-arrow left abs"><svg width="10" height="16"><path d="M8 2 2 8l6 6" stroke="#fff" stroke-width="2" fill="none"/></svg></div>
    <div class="hero-arrow right abs"><svg width="10" height="16"><path d="M2 2l6 6-6 6" stroke="#fff" stroke-width="2" fill="none"/></svg></div>
    <div class="hero-copy abs">
      <h1>Mindset Mastery.<br>Fitness Badassery.<br>Sustainable Nutrition</h1>
      <p>We focus on strong mindsets, fitness<br>and nutrition</p>
    </div>
  </section>

  <h2 class="section-title abs" style="top:888px">Welcome to Our Site</h2>
  <p class="welcome-text abs">Lorem ipsum dolor sit amet, consectetur adipiscing elit, sed do eiusmod tempor incididunt ut labore et dolore magna aliqua. Ut enim ad minim veniam, quis nostrud exercitation ullamco laboris nisi ut aliquip ex ea commodo consequat. Lorem ipsum dolor sit amet, consectetur adipiscing elit, sed do eiusmod tempor incididunt ut labore et dolore magna aliqua. Ut enim ad minim veniam, quis nostrud.</p>
  <div class="btn abs">Read More</div>
  <div class="divider abs"></div>

  <h2 class="section-title abs" style="top:1152px">View <em>Pictures</em></h2>
  <p class="pictures-sub abs">Neque porro quisquam est qui dolorem ipsum quia dolor sit</p>
  <div class="gallery abs" style="left:130px;background:linear-gradient(#8fb6d8,#d88aa6)" role="img" aria-label="Women stretching together in an aerobics class"></div>
  <div class="gallery abs" style="left:370px;background:linear-gradient(#5a5a5a,#3a3a3a)" role="img" aria-label="Two people doing squats in a dark studio"></div>
  <div class="gallery abs" style="left:610px;background:linear-gradient(#c9c9c9,#6b6b6b)" role="img" aria-label="Woman doing push-ups in a gym"></div>
  <div class="gallery abs" style="left:852px;background:linear-gradient(#bcd7e6,#c99a58)" role="img" aria-label="Runner resting on a sunlit rooftop"></div>

  <h2 class="blog-title abs">Blog Post</h2>
  <div class="blog-nav abs" style="left:1002px"><svg width="8" height="11"><path d="M6 1 2 5.5 6 10" stroke="#fff" stroke-width="2" fill="none"/></svg></div>
  <div class="blog-nav abs" style="left:1032px"><svg width="8" height="11"><path d="M2 1l4 4.5L2 10" stroke="#fff" stroke-width="2" fill="none"/></svg></div>

  <div class="post abs" style="left:130px">Lorem ipsum dolor sit amet, consectetur adipiscing elit, sed do eiusmod tempoer incididunt ut labore et dolore magna sit aliqua sed do eiusmod.</div>
  <div class="post abs" style="left:455px">Lorem ipsum dolor sit amet, consectetur adipiscing elit, sed do eiusmod tempoer incididunt ut labore et dolore magna sit aliqua sed do eiusmod.</div>
  <div class="post abs" style="left:778px">Lorem ipsum dolor sit amet, consectetur adipiscing elit, sed do eiusmod tempoer incididunt ut labore et dolore magna sit aliqua sed do eiusmod.</div>

  <div class="author abs" style="left:134px"><div class="avatar" role="img" aria-label="Author portrait"></div><div><b>JHONNY</b><i>dolore magna aliqua</i></div></div>
  <div class="author abs" style="left:460px"><div class="avatar" role="img" aria-label="Author portrait"></div><div><b>BELLA</b><i>dolore magna aliqua</i></div></div>
  <div class="author abs" style="left:782px"><div class="avatar" role="img" aria-label="Author portrait"></div><div><b>STELLA</b><i>dolore magna aliqua</i></div></div>

  <section class="video abs" role="img" aria-label="Woman training on an elliptical machine in a gym">
    <h2>Featured Video</h2>
    <svg width="80" height="80" viewBox="0 0 80 80"><circle cx="40" cy="40" r="36" fill="none" stroke="#fff" stroke-width="5"/><path d="M32 25v30l24-15z" fill="#fff"/></svg>
  </section>

  <footer class="site-footer abs">
    <div class="footer-links abs"><span>Home</span><span>|</span><span>About us</span><span>|</span><span>Site map</span><span>|</span><span>Contact us</span></div>
    <div class="copyright abs">©2014. Yoursite. All Right Reserved.</div>
    <div class="social-foot abs"><span></span><span></span><span></span><span></span><span></span></div>
  </footer>
</div>
</body>
</html>
```